RWT Fittings Ltd Business Cards

We need a business card with our business logo. We provide window and door installations on high-rises in west coast British Colombia, Canada.

I would like my business information and details on one side of the card, and the other side the company name with logo

Target Market(s)

General Contractors

Industry/Entity Type

Construction

Contact Information for Business Card

one side i want my company name and logo in the dark theme logo that i provided

Requirements
Must have
• Marco Peltieri, 16045518293, RWTFittings@mailbox-demo.com, 1407-5194 Linden Row Burnaby BC, V5H 2K9, Owner & Manager

```html
<!DOCTYPE html>
<html lang="en">
<head>
<meta charset="utf-8">
<title>RWT Fittings Ltd — Business Cards</title>
<link rel="stylesheet" href="https://fonts.googleapis.com/css2?family=Montserrat:wght@500;600;800&family=Roboto:wght@400;500&display=swap">
<style>
  :root {
    --stage: #222222;
    --card-white: #ffffff;
    --brand-blue: #29abe2;
    --brand-grey: #9b9b9b;
    --back-grey: #8f8f8f;
    --back-grey-light: #a4a4a4;
    --ink: #111111;
    --on-colour: #ffffff;
  }
  * { box-sizing: border-box; margin: 0; padding: 0; }
  html, body {
    width: 1200px; height: 780px; overflow: hidden;
    background: var(--stage);
  }
  .sheet {
    position: relative; width: 1200px; height: 780px;
    display: flex; align-items: center; justify-content: center; gap: 40px;
  }
  .card {
    position: relative; width: 540px; height: 310px; overflow: hidden;
    box-shadow: 0 10px 30px rgba(0,0,0,.45);
  }

  /* Front */
  .card--front { background: var(--card-white); }
  .brand {
    position: absolute; left: 118px; top: 62px;
    display: flex; align-items: center; gap: 12px;
    white-space: nowrap;
  }
  .brand__square { width: 30px; height: 30px; background: var(--brand-blue); }
  .brand__name {
    font-family: "Montserrat", sans-serif; font-weight: 600;
    font-size: 32px; letter-spacing: .5px; color: var(--brand-blue);
  }
  .contact-band {
    position: absolute; left: 256px; right: 0; top: 150px; height: 64px;
    background: var(--brand-blue);
    padding: 10px 0 0 18px;
    font-family: "Roboto", sans-serif; font-size: 14px; color: var(--on-colour);
    white-space: nowrap;
  }
  .contact-band__row { display: flex; align-items: center; gap: 8px; line-height: 22px; }
  .contact-band__icon { width: 13px; height: 13px; flex: none; }
  .identity-band {
    position: absolute; left: 0; width: 250px; top: 198px; height: 76px;
    background: var(--brand-grey);
    padding: 12px 0 0 28px; color: var(--on-colour);
    white-space: nowrap;
  }
  .identity-band__name {
    font-family: "Montserrat", sans-serif; font-weight: 800; font-size: 25px; line-height: 30px;
  }
  .identity-band__role {
    font-family: "Montserrat", sans-serif; font-weight: 500; font-size: 14px;
    padding-left: 46px; line-height: 20px;
  }
  .address {
    position: absolute; left: 196px; bottom: 12px;
    font-family: "Roboto", sans-serif; font-size: 14.5px; color: var(--ink);
    white-space: nowrap;
  }

  /* Back */
  .card--back { background: var(--back-grey); }
  .back-texture {
    position: absolute; inset: 0;
    background: radial-gradient(ellipse at 40% 35%, var(--back-grey-light), var(--back-grey) 70%);
  }
  .back-brand {
    position: absolute; right: 30px; bottom: 60px;
    font-family: "Montserrat", sans-serif; font-weight: 600; font-size: 16px;
    color: var(--on-colour); white-space: nowrap;
  }
</style>
</head>
<body>
<main class="sheet">
  <section class="card card--front" aria-label="Business card front">
    <div class="brand">
      <span class="brand__square"></span>
      <span class="brand__name">RWT Fittings Ltd</span>
    </div>

    <div class="contact-band">
      <div class="contact-band__row">
        <svg class="contact-band__icon" viewBox="0 0 24 24" aria-hidden="true"><path fill="#fff" d="M6.6 10.8a15.1 15.1 0 0 0 6.6 6.6l2.2-2.2c.3-.3.7-.4 1-.2 1.1.4 2.3.6 3.6.6.6 0 1 .4 1 1V20c0 .6-.4 1-1 1A17 17 0 0 1 3 4c0-.6.4-1 1-1h3.5c.6 0 1 .4 1 1 0 1.3.2 2.5.6 3.6.1.3 0 .7-.2 1z"/></svg>
        <span>1604 551 8293</span>
      </div>
      <div class="contact-band__row">
        <svg class="contact-band__icon" viewBox="0 0 24 24" aria-hidden="true"><path fill="#fff" d="M2 5h20v14H2z"/><path fill="none" stroke="#29abe2" stroke-width="2" d="M3 6l9 7 9-7"/></svg>
        <span>RWTFittings@mailbox-demo.com</span>
      </div>
    </div>

    <div class="identity-band">
      <p class="identity-band__name">Marco Peltieri</p>
      <p class="identity-band__role">Owner &amp; Manager</p>
    </div>

    <p class="address">1407-5194 Linden Row Burnaby BC, V5H 2K9</p>
  </section>

  <section class="card card--back" aria-label="Business card back">
    <div class="back-texture" role="img" aria-label="Embossed repeating brand pattern across the grey card back"></div>
    <p class="back-brand">RWT Fittings Ltd</p>
  </section>
</main>
</body>
</html>
```